Marlowe Group needs a business card

I would like the card to be simple but modern and elegant.
I like black and white.
or black and gold.
we are a private finance lender and also are involved in property and property developments.

please look at the business card photos i provided i would like M.G only one one side and all the other details on the other side use fonts that tie in with my theme.

Industry/Entity Type

Finance

Contact Information for Business Card

Marlowe Group (M.G) Daniel Marlowe M: 0413586207 E: danmarl@inboxmail.test

Font styles to use
Other font styles liked:
• Use fonts that would reflect our business

Colors
000000
ffffff

Requirements
Must have
• one side of details
• other side has either M.G or Marlowe Group like in the photos provided

```html
<!DOCTYPE html>
<html lang="en">
<head>
<meta charset="utf-8">
<title>Marlowe Group — Business Card</title>
<link rel="stylesheet" href="https://fonts.googleapis.com/css2?family=Open+Sans:ital,wght@0,400;0,700;1,400&display=swap">
<style>
  :root {
    --ink: #000000;
    --paper: #ffffff;
    --backdrop: #ececec;
    --muted: #555555;
    --shadow: rgba(0, 0, 0, 0.18);
  }
  * { box-sizing: border-box; margin: 0; padding: 0; }
  html, body {
    width: 1200px;
    height: 987px;
    overflow: hidden;
    background: var(--backdrop);
    font-family: "Open Sans", Arial, sans-serif;
  }
  .canvas {
    position: relative;
    width: 1200px;
    height: 987px;
  }
  .card {
    position: absolute;
    left: 293px;
    width: 615px;
    height: 351px;
    box-shadow: 0 2px 6px var(--shadow);
  }
  .card--front {
    top: 130px;
    background: var(--paper);
  }
  .card--back {
    top: 506px;
    background: var(--ink);
    display: flex;
    align-items: center;
    justify-content: center;
  }
  .brand-name {
    position: absolute;
    top: 72px;
    left: 0;
    width: 100%;
    text-align: center;
    font-weight: 700;
    font-size: 40px;
    line-height: 56px;
    color: var(--ink);
    text-transform: uppercase;
    letter-spacing: 1px;
  }
  .name-band {
    position: absolute;
    top: 197px;
    left: 0;
    width: 100%;
    height: 55px;
    background: var(--ink);
    color: var(--paper);
    display: flex;
    align-items: center;
    justify-content: center;
    font-weight: 700;
    font-size: 23px;
  }
  .contact {
    position: absolute;
    top: 274px;
    left: 0;
    width: 100%;
    text-align: center;
    color: var(--muted);
    font-size: 17px;
    line-height: 26px;
  }
  .contact__divider { margin: 0 6px; }
  .contact__web { font-style: italic; }
  .monogram {
    color: var(--paper);
    font-weight: 700;
    font-size: 100px;
    letter-spacing: 2px;
    line-height: 1;
  }
</style>
</head>
<body>
  <main class="canvas">
    <section class="card card--front" aria-label="Card front">
      <h1 class="brand-name">Marlowe Group</h1>
      <div class="name-band">Daniel Marlowe</div>
      <div class="contact">
        <p>0413586207<span class="contact__divider">|</span>danmarl@inboxmail.test</p>
        <p class="contact__web">www.marlowegroup.test</p>
      </div>
    </section>
    <section class="card card--back" aria-label="Card back">
      <p class="monogram">M.G</p>
    </section>
  </main>
</body>
</html>
```